Business Card Design Project

I need a business card designed from scratch. I have an existing logo that I can upload in Illustrator for modification or redesign.

The Company is called Query Lanterns http://querylanterns.com.au and we provide Search Engine Optimization services to Australian businesses. The current logo signifies an increase in visitors, profits etc...

There are no restrictions as to the redesign - colours, style etc are all open to change.

Cards will be full colour and one sided printed at http://www.cardmoxel.com.au so check their requirements for file format and sizes etc.

I will expect all original files upon completion of project.

Target Market(s)

Any business with a web site looking to improve their search engine rankings

Industry/Entity Type

Business

Requirements
Must have
• I like modern, sleek designs. Clean, not fussy, uncluttered.

```html
<!DOCTYPE html>
<html lang="en">
<head>
<meta charset="utf-8">
<title>Query Lanterns – Business Cards</title>
<link rel="stylesheet" href="https://fonts.googleapis.com/css2?family=Open+Sans:wght@400;600;700;800&display=swap">
<style>
  :root {
    --brand-blue: #1b6fb3;
    --brand-navy: #1f4f86;
    --brand-yellow: #f4c316;
    --text-grey: #5a5a5a;
    --divider: #d6d6d6;
    --card-white: #ffffff;
    --stage: #ecebe8;
  }
  * { box-sizing: border-box; margin: 0; padding: 0; }
  html, body {
    width: 1200px;
    height: 460px;
    overflow: hidden;
    background: var(--stage);
    font-family: "Open Sans", Arial, sans-serif;
  }
  .canvas {
    position: relative;
    width: 1200px;
    height: 460px;
  }
  .card {
    position: absolute;
    top: 78px;
    width: 540px;
    height: 300px;
    background: var(--card-white);
    border-radius: 16px;
    box-shadow: 0 2px 6px rgba(0,0,0,0.18);
  }
  .card--front { left: 44px; }
  .card--back { left: 616px; }

  .brand {
    position: absolute;
    display: flex;
    align-items: center;
    gap: 10px;
  }
  .brand__dot {
    width: 16px;
    height: 16px;
    border-radius: 50%;
    background: var(--brand-yellow);
    flex: none;
  }
  .brand__name {
    color: var(--brand-blue);
    font-weight: 800;
    font-size: 26px;
    letter-spacing: -0.3px;
    line-height: 1;
    white-space: nowrap;
  }
  .card--front .brand { left: 24px; top: 133px; }
  .card--front .brand__name { font-size: 24px; }

  .divider {
    position: absolute;
    left: 290px;
    top: 52px;
    width: 1px;
    height: 178px;
    background: linear-gradient(to bottom, transparent, var(--divider) 15%, var(--divider) 85%, transparent);
  }

  .details {
    position: absolute;
    left: 304px;
    top: 50px;
    color: var(--text-grey);
    font-size: 13px;
    line-height: 1.4;
  }
  .details__name {
    color: var(--brand-blue);
    font-weight: 700;
    font-size: 17px;
    line-height: 1.2;
  }
  .details__title { margin-bottom: 18px; }
  .contact-list { list-style: none; margin-bottom: 14px; }
  .contact-list li {
    display: flex;
    align-items: center;
    gap: 6px;
    height: 18px;
  }
  .contact-list svg { width: 9px; height: 9px; fill: var(--brand-navy); flex: none; }
  .address { line-height: 1.45; }

  .card--back .brand {
    left: 0;
    right: 0;
    top: 120px;
    justify-content: center;
  }
  .card--back .brand__name { font-size: 30px; }
  .web-address {
    position: absolute;
    left: 0;
    right: 0;
    top: 196px;
    text-align: center;
    font-size: 13px;
    letter-spacing: 2.2px;
    color: var(--text-grey);
  }
  .web-address__domain { color: var(--brand-blue); }
</style>
</head>
<body>
<main class="canvas">

  <section class="card card--front" aria-label="Card front">
    <div class="brand">
      <span class="brand__dot"></span>
      <span class="brand__name">Query Lanterns</span>
    </div>

    <div class="divider"></div>

    <div class="details">
      <p class="details__name">Your Name</p>
      <p class="details__title">Title</p>
      <ul class="contact-list">
        <li>
          <svg viewBox="0 0 10 10" aria-hidden="true"><circle cx="5" cy="5" r="5"/><path d="M3 2.5l1 .2.3 1.2-.6.5a4 4 0 0 0 1.9 1.9l.5-.6 1.2.3.2 1c-.6.6-1.7.5-3-.5S2.4 3.8 3 2.5z" fill="#fff"/></svg>
          <span>098 765 4321</span>
        </li>
        <li>
          <svg viewBox="0 0 10 10" aria-hidden="true"><rect x="2.5" y="0.5" width="5" height="9" rx="1"/><rect x="3.3" y="1.6" width="3.4" height="5.2" fill="#fff"/></svg>
          <span>098 765 4321</span>
        </li>
        <li>
          <svg viewBox="0 0 10 10" aria-hidden="true"><rect x="0.5" y="2" width="9" height="6.5" rx="0.6"/><path d="M0.8 2.4 5 5.6l4.2-3.2" stroke="#fff" stroke-width="0.9" fill="none"/></svg>
          <span>enquiry@querylanterns.com.au</span>
        </li>
        <li>
          <svg viewBox="0 0 10 10" aria-hidden="true"><circle cx="5" cy="5" r="4.6"/><path d="M0.6 5h8.8M5 0.5v9M5 0.5c-2.2 2.4-2.2 6.6 0 9M5 0.5c2.2 2.4 2.2 6.6 0 9" stroke="#fff" stroke-width="0.6" fill="none"/></svg>
          <span>www.querylanterns.com.au</span>
        </li>
      </ul>
      <p class="address">00Floor Street, City Name<br>State Name, Contry Name</p>
    </div>
  </section>

  <section class="card card--back" aria-label="Card back">
    <div class="brand">
      <span class="brand__dot"></span>
      <span class="brand__name">Query Lanterns</span>
    </div>
    <p class="web-address">www.<span class="web-address__domain">querylanterns</span>.com.au</p>
  </section>

</main>
</body>
</html>
```